Eye Catching Email Marketing design

Our health care consulting firm is based in New York City. We sell health care consulting Services to medical practices (doctors). We need a powerful email marketing design to use as one of our primary selling tools to attract new clients. The Design should convey health care knowledge, expertise professionalism, cutting edge technology and the services we offer. <br/>The design should incorporate our logo and its colors (blue and white) but we want it to be eye catching and vibrant, so other colors be included. We are open to the designer's creativity. Any pictures used should show diversity (races)and should include women. Designers can find our logo and other graphics on our website at www harbor ridge advisory.com. Please feel free to ask questions.<br/><br/>

Target Market(s)

Health care professionals, executives and Doctors.

Colors

Designer to choose colors to be used in the design.

Requirements
Nice to have
• What ever the design feels will help make this design vibrant

```html
<!DOCTYPE html>
<html lang="en">
<head>
<meta charset="utf-8">
<title>Harbor Ridge Advisory – Email</title>
<link href="https://fonts.googleapis.com/css2?family=Lato:wght@300;400;700;900&display=swap" rel="stylesheet">
<style>
  :root{
    --navy:#0b3e91;
    --sky:#2a8fd0;
    --ink:#2e2e2e;
    --mist:#f3f3f3;
    --rule:#cfcfcf;
    --white:#ffffff;
    --band-a:#0a2e78;
    --band-b:#1b4fa6;
  }
  *{box-sizing:border-box;margin:0;padding:0}
  html,body{width:1200px;height:3668px;overflow:hidden;background:var(--white);font-family:"Lato",sans-serif;color:var(--ink)}
  .hero-photo{height:628px;background:linear-gradient(135deg,#e9ecef 0%,#d6d9dc 40%,#b9bcc0 70%,#c9434f 100%)}
  .masthead{height:172px;display:flex;align-items:center;justify-content:space-between;padding:0 28px 0 30px}
  .brand{display:flex;align-items:center;gap:16px;color:var(--navy);font-weight:700;font-size:34px}
  .brand-mark{width:40px;height:40px;background:var(--navy)}
  .masthead-phone{display:flex;align-items:center;gap:22px;font-weight:700;font-size:48px;color:#333}
  .welcome{background:var(--mist);height:674px;text-align:center;padding-top:66px}
  .welcome h1{color:var(--navy);font-weight:900;font-size:57px;line-height:65px}
  .welcome p{font-size:27px;line-height:49.5px;margin:28px 30px 0}
  .btn{display:inline-flex;align-items:center;justify-content:center;background:var(--sky);color:var(--white);font-weight:700;text-decoration:none}
  .btn-lg{width:355px;height:88px;font-size:44px}
  .welcome .btn{margin-top:40px}
  .services{position:relative;height:1331px}
  .services .divider-v{position:absolute;left:607px;top:89px;width:2px;height:1159px;background:var(--rule)}
  .services .divider-h{position:absolute;left:28px;top:672px;width:1144px;height:2px;background:var(--rule)}
  .service{position:absolute;width:600px;text-align:center}
  .service .icon{display:block;margin:0 auto;width:117px;height:117px}
  .service h2{color:var(--navy);font-weight:700;font-size:38px;line-height:48px;margin-top:28px}
  .service p{font-size:26px;line-height:49.5px;margin:8px 30px 0}
  .service .btn{position:absolute;left:178px;width:245px;height:87px;font-size:31px}
  .row1{top:86px;height:600px}.row1 .btn{top:444px}
  .row2{top:716px;height:600px}.row2 .btn{top:447px}
  .col1{left:0}.col2{left:600px}
  .contact{height:573px;background:linear-gradient(120deg,var(--band-a),var(--band-b) 55%,var(--band-a));text-align:center;color:var(--white);padding-top:106px}
  .contact h2{font-weight:900;font-size:58px;line-height:64px}
  .contact .lead{font-weight:300;font-size:38px;margin-top:12px}
  .contact-line{display:flex;justify-content:center;align-items:center;gap:26px;font-weight:700;font-size:37px;margin-top:24px}
  .contact-line span{display:flex;align-items:center;gap:18px}
  .contact .btn{margin-top:42px}
  .footer{text-align:center;padding-top:73px}
  .footer small{font-size:24px}
  .social{display:flex;justify-content:center;gap:20px;margin-top:48px}
  .social i{display:block;width:67px;height:67px;border-radius:50%}
  .s1{background:#2d5aa8}.s2{background:#5bbde6}.s3{background:#0b3e91}.s4{background:#b0127a}
</style>
</head>
<body>
  <div class="hero-photo" role="img" aria-label="Photo of a diverse team of doctors and a consultant meeting around a white table"></div>

  <header class="masthead">
    <div class="brand"><span class="brand-mark"></span>Harbor Ridge Advisory</div>
    <div class="masthead-phone">
      <svg width="40" height="40" viewBox="0 0 24 24"><path fill="#2a8fd0" d="M6.6 10.8a15.1 15.1 0 0 0 6.6 6.6l2.2-2.2c.3-.3.7-.4 1-.2 1.1.4 2.3.6 3.6.6.6 0 1 .4 1 1V20c0 .6-.4 1-1 1A17 17 0 0 1 3 4c0-.6.4-1 1-1h3.5c.6 0 1 .4 1 1 0 1.3.2 2.5.6 3.6.1.3 0 .7-.2 1z"/></svg>
      (212) 555-0148
    </div>
  </header>

  <section class="welcome">
    <h1>Welcome<br>Harbor Ridge Advisory</h1>
    <p>Harbor Ridge Advisory (HRA), founded in 2015, is a Management Services Organization &amp; Healthcare Consulting Firm skilled at helping medical practices advance their strategic vision in an ever-evolving healthcare system. Harbor Ridge Advisory specializes in Revenue Cycle Management, Practice Management, Compliance Management &amp; Healthcare Innovation.</p>
    <a class="btn btn-lg" href="#">Get A Quote</a>
  </section>

  <section class="services">
    <div class="divider-v"></div>
    <div class="divider-h"></div>

    <article class="service row1 col1">
      <svg class="icon" viewBox="0 0 100 100" fill="none" stroke="#2a8fd0" stroke-width="11"><path d="M18 62a34 34 0 0 1 46-41"/><path d="M82 38a34 34 0 0 1-46 41"/><path fill="#2a8fd0" stroke="none" d="M58 8l18 14-22 6z M42 92L24 78l22-6z"/></svg>
      <h2>Revenue Cycle Management</h2>
      <p>Harbor Ridge Advisory understands the reimbursement landscape and is skilled in helping medical practices improve their margins.</p>
      <a class="btn" href="#">Read More</a>
    </article>

    <article class="service row1 col2">
      <svg class="icon" viewBox="0 0 100 100"><path fill="#2a8fd0" d="M20 6h58v80H34a12 12 0 0 1-12-12V20a8 8 0 0 0-8-8V6z"/><path fill="#2a8fd0" d="M40 80h52v10a6 6 0 0 1-6 6H40z"/><path fill="#fff" d="M50 26l16 6v12c0 10-7 16-16 20-9-4-16-10-16-20V32z"/><path fill="none" stroke="#2a8fd0" stroke-width="5" d="M42 44l6 6 11-12"/></svg>
      <h2>Compliance Management</h2>
      <p>In a heavily regulated healthcare environment, medical practices need to be acutely aware of regulations or face huge fines.</p>
      <a class="btn" href="#">Read More</a>
    </article>

    <article class="service row2 col1">
      <svg class="icon" viewBox="0 0 100 100"><circle cx="50" cy="34" r="28" fill="none" stroke="#2a8fd0" stroke-width="12" stroke-dasharray="10 6"/><rect x="38" y="26" width="24" height="26" rx="4" fill="#2a8fd0"/><rect x="6" y="62" width="14" height="32" fill="#2a8fd0"/><path fill="#2a8fd0" d="M24 64h30c6 0 6 8 0 8H40h22l26-10c6-2 9 5 4 8L62 90H24z"/></svg>
      <h2>Healthcare Innovation</h2>
      <p>Do you want to enhance clinical operations and workflows? Are you looking to expand patient access and improve margins?</p>
      <a class="btn" href="#">Read More</a>
    </article>

    <article class="service row2 col2">
      <svg class="icon" viewBox="0 0 100 100"><circle cx="50" cy="24" r="15" fill="none" stroke="#2a8fd0" stroke-width="9" stroke-dasharray="6 4"/><path fill="#2a8fd0" d="M6 44l10-4 14 24 12 10v24H28V80L8 60z M94 44l-10-4-14 24-12 10v24h14V80l20-20z"/></svg>
      <h2>Practice Management</h2>
      <p>Practice Management requires the right balance of skill, knowledge, management &amp; business expertise. HRA can help strategically grow your practice.</p>
      <a class="btn" href="#">Read More</a>
    </article>
  </section>

  <section class="contact" role="img" aria-label="Blue-tinted photo of professionals working at laptops, behind contact details">
    <h2>Get in Touch</h2>
    <p class="lead">Talk to a Member of Our Team.</p>
    <div class="contact-line">
      <span><svg width="34" height="34" viewBox="0 0 24 24"><path fill="#fff" d="M6.6 10.8a15.1 15.1 0 0 0 6.6 6.6l2.2-2.2c.3-.3.7-.4 1-.2 1.1.4 2.3.6 3.6.6.6 0 1 .4 1 1V20c0 .6-.4 1-1 1A17 17 0 0 1 3 4c0-.6.4-1 1-1h3.5c.6 0 1 .4 1 1 0 1.3.2 2.5.6 3.6.1.3 0 .7-.2 1z"/></svg>(212) 555-0148</span>
      <span><svg width="38" height="30" viewBox="0 0 24 18"><rect x="1" y="1" width="22" height="16" rx="2" fill="#fff"/><path d="M2 3l10 7 10-7" fill="none" stroke="#1b4fa6" stroke-width="2"/></svg>info@harborridgeadvisory.com</span>
    </div>
    <a class="btn btn-lg" href="#">Contact Us</a>
  </section>

  <footer class="footer">
    <small>Copyright © 2020 Company Name All Right Reserved</small>
    <div class="social"><i class="s1"></i><i class="s2"></i><i class="s3"></i><i class="s4"></i></div>
  </footer>
</body>
</html>
```